Brochure for people who suffer from Sleep Apnea and need a medical device called a CPAP Machine

I want a brochure that can be placed in doctors offices with my competitors brochures. It needs to be bold and stand out and deliver a very strong message that draws the patients away from our competitors and to us. I have included a word document generally outlining some of my requirements and thoughts, please review prior to investing time into design!

Target Market(s)

people who suffer from sleep apnea, which is a disease that causes them to stop breathing many times per hour, resulting in the patient needing to wear a device called a CPAP Machine. This is an illness that can impact anyone but is more likely to impact those suffering from obesity and men.

Industry/Entity Type

Health Care

Other font styles liked:
• Use what you think is best

Colors

Designer to choose colors to be used in the design.

Requirements
Must have
• Please see word document for must have items, and feel free to contact me with any questions.
• Also must have bold colors, and/or graphics to really stand out among my competitors brochures.
Nice to have
• Would prefer to use the baby picture titled "sleeping baby 4" if possible but provided 2 other baby photos just in case. Whatever you want to add, use your professional creativity! You Don't need to use all the pictures uploaded!!!!!
Should not have
• Nothing discriminatory or offensive.

```html
<!DOCTYPE html>
<html lang="en">
<head>
<meta charset="utf-8">
<title>RestWell Airway – Trifold Brochure</title>
<link href="https://fonts.googleapis.com/css2?family=Cabin:wght@400;600;700&family=Signika:wght@400;600;700&family=Bree+Serif&family=Courgette&display=swap" rel="stylesheet">
<style>
:root{
  --purple:#6c2b88;
  --purple-dark:#4a175f;
  --purple-light:#8e4fa8;
  --green:#2ea866;
  --green-dark:#16744a;
  --green-text:#3aa86a;
  --ink:#3c3c3c;
  --canvas:#d4d5d7;
  --white:#ffffff;
  --seal-gold:#f1c23a;
  --seal-red:#c0392b;
}
*{box-sizing:border-box;margin:0;padding:0}
html,body{width:916px;height:1200px;overflow:hidden;background:var(--canvas)}
body{font-family:"Cabin",sans-serif;color:var(--ink);position:relative}
.sheet{position:absolute;left:149px;width:656px;height:510px;background:var(--white);box-shadow:0 10px 14px -6px rgba(0,0,0,.45);overflow:hidden}
.sheet--outside{top:54px}
.sheet--inside{top:616px}
.panel{position:absolute;top:0;height:100%;overflow:hidden}
.photo{position:absolute}
.abs{position:absolute}
.brand{font-family:"Signika",sans-serif;font-weight:600;white-space:nowrap}
.pill{position:absolute;background:var(--purple-dark);color:var(--white);border-radius:10px;display:flex;align-items:center;justify-content:center;gap:6px;font-family:"Signika",sans-serif;box-shadow:1px 2px 3px rgba(0,0,0,.35);white-space:nowrap}
.pill svg{width:12px;height:12px}
.web{position:absolute;font-family:"Signika",sans-serif;font-weight:600;letter-spacing:1.2px;color:var(--green-dark);font-size:9px;text-align:center;white-space:nowrap}
.script{font-family:"Courgette",cursive}

/* outside left panel */
.services{left:0;width:214px;background:linear-gradient(90deg,#fff 60%,#eeeeee)}
.services .intro{position:absolute;left:7px;right:10px;color:var(--green-text);font-size:7.2px;line-height:1.35}
.service{position:absolute;left:7px;right:8px;display:flex;gap:6px}
.service .badge{flex:0 0 26px;height:26px;border-radius:50%;background:var(--purple);border:2px solid #d9c5e2;display:flex;align-items:center;justify-content:center}
.service .badge svg{width:13px;height:13px}
.service h4{font-family:"Signika",sans-serif;font-weight:600;font-size:7.2px;color:var(--purple);line-height:1.1}
.service p{font-size:6.3px;line-height:1.25;color:var(--ink)}
.services .closing{position:absolute;left:10px;font-size:7px;color:var(--purple);white-space:nowrap}
.services .tagline{position:absolute;left:10px;font-size:10.5px;color:var(--green-dark);white-space:nowrap}

/* outside middle panel */
.cover-mid{left:214px;width:216px;background:linear-gradient(180deg,var(--green) 30%,var(--green-dark));color:var(--white);text-align:center}
.cover-mid .center{position:absolute;left:0;right:0}
.seal{position:absolute;left:64px;top:270px;width:88px;height:58px;border-radius:8px;background:radial-gradient(ellipse at 50% 45%,var(--seal-gold) 45%,var(--seal-red) 100%)}

/* outside right panel */
.cover{left:430px;width:226px;background:linear-gradient(180deg,#fff,#f3f3f3)}
.cover .center{position:absolute;left:0;right:0;text-align:center}

/* inside */
.differ{left:0;width:219px;background:linear-gradient(180deg,var(--purple-dark),var(--purple-light) 80%);color:var(--white)}
.differ .tab{position:absolute;left:0;top:108px;width:160px;height:25px;background:var(--green-dark);border-radius:0 13px 13px 0;font-family:"Signika",sans-serif;font-weight:600;font-size:11px;line-height:25px;padding-left:8px;box-shadow:1px 2px 3px rgba(0,0,0,.3)}
.differ ul{position:absolute;left:9px;top:150px;list-style:none}
.differ li{font-size:9px;height:16.4px;display:flex;align-items:center;gap:6px;white-space:nowrap}
.differ li::before{content:"";width:7px;height:7px;border-radius:50%;background:var(--green)}
.promise{left:219px;width:213px;background:linear-gradient(90deg,#fff 70%,#efefef);text-align:center}
.promise .head{position:absolute;left:6px;right:6px;top:37px;color:var(--green-text);font-size:10px;line-height:1.3}
.step-icon{position:absolute;left:83px;width:46px;height:46px;border-radius:50%;border:2px solid #ddd;background:#fff;display:flex;align-items:center;justify-content:center;box-shadow:0 2px 2px rgba(0,0,0,.12)}
.step-icon svg{width:22px;height:22px}
.step-text{position:absolute;left:12px;right:12px;font-size:7px;line-height:1.42}
.detail{left:432px;width:224px;background:linear-gradient(180deg,var(--purple-light),var(--purple-dark));color:var(--white)}
.detail .copy{position:absolute;left:10px;right:12px;font-size:7.2px;line-height:1.36}
.detail .big{font-size:8.8px;line-height:1.4}
.detail .script{color:#5fd48f;font-size:9.8px;line-height:1.35}
</style>
</head>
<body>

<section class="sheet sheet--outside">

  <div class="panel services">
    <div class="photo" style="left:0;top:0;width:214px;height:190px;background:radial-gradient(circle at 55% 55%,#f6e2d6,#e9e6e6 70%)" role="img" aria-label="Photo of a smiling newborn baby sleeping"></div>
    <svg class="abs" style="left:0;top:0" width="214" height="110" viewBox="0 0 214 110" aria-hidden="true">
      <path d="M0 0H214V36C150 26 70 40 0 104Z" fill="var(--purple)"/>
      <path d="M0 104C70 40 150 26 214 36V42C150 34 70 50 0 112Z" fill="var(--green)"/>
    </svg>
    <p class="intro" style="top:198px">Anyone can give you CPAP supplies. However we are committed to providing you with exceptional customer service too.</p>
    <p class="intro" style="top:229px">How do we do this?<br>By giving you services no other CPAP retailer offers, like…</p>

    <div class="service" style="top:259px"><span class="badge"><svg viewBox="0 0 24 24"><path d="M3 12L12 4l9 8v9H3z" fill="#fff"/></svg></span><div><h4>FREE HOME VISITS</h4><p>We bring the store to you so we can give you as much time as you need and set up all your equipment and supplies for you.</p></div></div>
    <div class="service" style="top:296px"><span class="badge"><svg viewBox="0 0 24 24"><path d="M2 6h13v10H2zM15 10h4l3 3v3h-7z" fill="#fff"/><circle cx="6" cy="18" r="2" fill="#fff"/><circle cx="18" cy="18" r="2" fill="#fff"/></svg></span><div><h4>FREE DELIVERY</h4><p>So you never need to come to the store (Unless you want to!).</p></div></div>
    <div class="service" style="top:334px"><span class="badge"><svg viewBox="0 0 24 24"><rect x="4" y="5" width="16" height="15" fill="none" stroke="#fff" stroke-width="2"/><path d="M8 13l3 3 5-6" fill="none" stroke="#fff" stroke-width="2"/></svg></span><div><h4>NIGHT AND WEEKEND APPOINTMENTS</h4><p>Because not everyone works 9-to-5.</p></div></div>
    <div class="service" style="top:371px"><span class="badge"><svg viewBox="0 0 24 24"><circle cx="12" cy="8" r="4" fill="#fff"/><path d="M4 20c0-5 16-5 16 0z" fill="#fff"/></svg></span><div><h4>A DEDICATED CLINICIAN</h4><p>Because we also want to be your friend.</p></div></div>
    <div class="service" style="top:403px"><span class="badge"><svg viewBox="0 0 24 24"><ellipse cx="12" cy="14" rx="8" ry="6" fill="#fff"/><circle cx="12" cy="5" r="2.5" fill="#fff"/></svg></span><div><h4>HARDSHIP AND FINANCIAL-ASSISTANCE PROGRAMS</h4><p>To make sure everyone gets the care they need.</p></div></div>
    <div class="service" style="top:439px"><span class="badge"><svg viewBox="0 0 24 24"><path d="M3 10h4v10H3zM8 10l4-7c2 0 2 2 2 3l-1 4h6c1 0 2 1 2 2l-2 7c0 1-1 1-2 1H8z" fill="#fff"/></svg></span><div><h4>PROMISE OF GUARANTEED SUCCESS</h4><p>We offer 30-day guarantees on all supplies so you know you are getting the best care possible.</p></div></div>

    <p class="closing" style="top:478px">Why are YOU Settling for LESS? Let US treat you RIGHT!</p>
    <p class="tagline script" style="top:490px">We Make CPAP Personal!</p>
  </div>

  <div class="panel cover-mid">
    <svg class="abs" style="left:0;top:0" width="216" height="110" viewBox="0 0 216 110" aria-hidden="true">
      <path d="M0 0H216V66C150 40 70 38 0 38Z" fill="var(--purple-light)"/>
      <path d="M0 38C70 38 150 40 216 66V70C150 44 70 42 0 42Z" fill="#fff" opacity=".7"/>
    </svg>
    <div class="photo" style="left:40px;top:24px;width:136px;height:136px;border-radius:50%;background:radial-gradient(circle,#c9b2a5,#2a2a2a 75%);border:4px solid #7ac99a" role="img" aria-label="Photo of a startled man wearing an awkward CPAP mask"></div>
    <p class="center brand" style="top:200px;font-size:22px;color:#fff">RestWell Airway</p>
    <p class="center" style="top:232px;font-family:Signika,sans-serif;font-weight:700;font-size:12px">CPAP Doesn't need to be like this!</p>
    <p class="center" style="top:250px;font-size:8.6px">Let us make sure this doesn't happen to you</p>
    <div class="seal" role="img" aria-label="100% satisfaction guarantee seal"></div>
    <p class="center" style="top:333px;font-size:9.8px;line-height:1.4">We Guarantee Your CPAP Success,<br>because your Success is our reputation.</p>
    <p class="center" style="top:364px;font-family:Signika,sans-serif;font-weight:600;font-size:8.8px">Call for an Appointment (Or just to talk) Today</p>
    <div class="pill" style="left:26px;top:382px;width:161px;height:21px;font-size:13px"><svg viewBox="0 0 24 24"><circle cx="12" cy="12" r="10" fill="none" stroke="#fff" stroke-width="2"/><path d="M8 7l2 0 1 3-1.5 1a7 7 0 0 0 3.5 3.5L14 13l3 1v2c-5 1-10-4-9-9z" fill="#fff"/></svg>555-014-2290</div>
    <p class="center" style="top:413px;font-size:8.8px;line-height:1.45">48 Harbour Lane<br>Lakeview, Ontario L0S 1A0<br>Serving all of Ontario</p>
    <p class="web" style="left:0;right:0;top:455px;color:#e8f5ec">www.RestWellAirway.com</p>
    <p class="center script" style="top:474px;font-size:13px">We Bring The Store To You</p>
  </div>

  <div class="panel cover">
    <p class="center brand" style="top:50px;font-size:21px;color:var(--green)"><span style="display:inline-block;width:9px;height:9px;border-radius:50%;background:var(--purple);margin-right:5px;vertical-align:middle"></span>RestWell Airway</p>
    <svg class="abs" style="left:0;top:70px" width="226" height="50" viewBox="0 0 226 50" aria-hidden="true">
      <path d="M0 50V44C70 44 150 30 226 8V22C150 40 70 50 0 50Z" fill="var(--purple)"/>
      <path d="M0 44C70 44 150 30 226 8V3C150 26 70 40 0 40Z" fill="var(--green)"/>
    </svg>
    <p class="center" style="top:127px;font-family:Signika,sans-serif;font-weight:700;font-size:19px;line-height:1.08;color:var(--green)">WANT SLEEP LIKE<br>A BABY AGAIN?</p>
    <p class="center" style="top:171px;font-size:16px;color:var(--purple)">Let us show You How!</p>
    <div class="photo" style="left:0;top:194px;width:226px;height:190px;background:linear-gradient(160deg,#e9e5e2,#c9b3a6 55%,#eeeeee)" role="img" aria-label="Photo of a happy couple in bed, the man wearing a comfortable CPAP mask"></div>
    <svg class="abs" style="left:0;top:360px" width="226" height="36" viewBox="0 0 226 36" aria-hidden="true">
      <path d="M0 0C60 28 160 26 226 4V36H0Z" fill="#f5f5f5"/>
      <path d="M0 0C60 28 160 26 226 4V10C160 32 60 34 0 8Z" fill="var(--purple)"/>
    </svg>
    <p class="center" style="top:411px;font-family:'Bree Serif',serif;font-size:15px;color:var(--purple)">We Bring The Store To You</p>
    <p class="center" style="top:438px;font-size:10.5px;color:var(--green-text)">Serving all of Ontario</p>
    <div class="pill" style="left:31px;top:459px;width:161px;height:21px;font-size:13px"><svg viewBox="0 0 24 24"><circle cx="12" cy="12" r="10" fill="none" stroke="#fff" stroke-width="2"/><path d="M8 7l2 0 1 3-1.5 1a7 7 0 0 0 3.5 3.5L14 13l3 1v2c-5 1-10-4-9-9z" fill="#fff"/></svg>555-014-2290</div>
    <p class="web" style="left:0;right:0;top:490px">www.RestWellAirway.com</p>
  </div>
</section>

<section class="sheet sheet--inside">

  <div class="panel differ">
    <p class="abs brand" style="left:20px;top:68px;font-size:21px;color:var(--green)">RestWell Airway</p>
    <div class="tab">What Makes us Different?</div>
    <ul>
      <li>Everything!</li>
      <li>Free Home Visits</li>
      <li>Free delivery</li>
      <li>Night and weekend appointments</li>
      <li>Specializes exclusively in Sleep Therapy</li>
      <li>A dedicated clinician assigned directly to you</li>
      <li>Hardship and financial-assistance programs</li>
    </ul>
    <div class="photo" style="left:0;top:300px;width:219px;height:210px;background:linear-gradient(160deg,#dfe3ea,#9aa3b3 60%,#2b3140)" role="img" aria-label="Photo of hands packing a CPAP machine into its travel case"></div>
    <svg class="abs" style="left:0;top:290px" width="219" height="40" viewBox="0 0 219 40" aria-hidden="true">
      <path d="M0 0H219V34C150 10 60 8 0 20Z" fill="#8b4ca6"/>
      <path d="M0 20C60 8 150 10 219 34V40C150 16 60 14 0 26Z" fill="#fff" opacity=".85"/>
    </svg>
  </div>

  <div class="panel promise">
    <p class="head">When you get diagnosed with Obstructive Sleep Apnea it can be overwhelming.<br>We are here to help. We will:</p>
    <div class="step-icon" style="top:94px"><svg viewBox="0 0 24 24"><path d="M2 12L11 4l9 8v8H2z" fill="var(--green)"/><circle cx="17" cy="14" r="3" fill="var(--green-dark)"/></svg></div>
    <p class="step-text" style="top:150px">Visit you in the comfort of your own home so we can privately discuss Sleep Apnea, explain what to expect next, and answer any and all your questions in a relaxed, comfortable environment.<br>You don't get this from any other CPAP Retailer.</p>
    <div class="step-icon" style="top:222px"><svg viewBox="0 0 24 24"><circle cx="14" cy="8" r="5" fill="none" stroke="var(--green)" stroke-width="3" stroke-dasharray="3 2"/><circle cx="8" cy="16" r="5" fill="none" stroke="var(--green)" stroke-width="3" stroke-dasharray="3 2"/></svg></div>
    <p class="step-text" style="top:279px">Figure out the best equipment and supplies you need to guarantee your success…<br>We will even set up everything for before we leave so you know it is set up right!</p>
    <div class="step-icon" style="top:331px"><svg viewBox="0 0 24 24"><path d="M3 10h4v10H3zM8 10l4-7c2 0 2 2 2 3l-1 4h6c1 0 2 1 2 2l-2 7c0 1-1 1-2 1H8z" fill="var(--green)"/></svg></div>
    <p class="step-text" style="top:388px">We are committed to your success.<br>We will spend as much time with you as necessary to make sure all your questions are answered and every concern is addressed.</p>
    <div class="pill" style="left:10px;top:443px;width:186px;height:19px;font-size:9.5px;letter-spacing:1px">Call Us <svg viewBox="0 0 24 24"><circle cx="12" cy="12" r="10" fill="none" stroke="#fff" stroke-width="2"/><path d="M8 7l2 0 1 3-1.5 1a7 7 0 0 0 3.5 3.5L14 13l3 1v2c-5 1-10-4-9-9z" fill="#fff"/></svg>555-014-2290</div>
    <p class="web" style="left:0;right:0;top:475px">www.RestWellAirway.com</p>
  </div>

  <div class="panel detail">
    <div class="photo" style="left:0;top:0;width:224px;height:215px;background:linear-gradient(150deg,#f0eeee,#c8aa98 50%,#e8e8e8)" role="img" aria-label="Photo of a man sleeping peacefully with a CPAP nasal mask"></div>
    <svg class="abs" style="left:0;top:140px" width="224" height="86" viewBox="0 0 224 86" aria-hidden="true">
      <path d="M0 86V74C80 74 170 50 224 0V86Z" fill="#8e4fa8"/>
      <path d="M0 74C80 74 170 50 224 0V8C170 58 80 80 0 80Z" fill="#cfcfcf"/>
    </svg>
    <p class="copy" style="top:236px">RestWell Airway is able to provide you with CPAP, APAP or BiPAP Machines to meet any need. Because all RestWell Airway does is CPAP, you can be guaranteed to get the most appropriate machine to meet your specific requirements.</p>
    <p class="copy" style="top:295px">RestWell Airway will also service your CPAP, APAP or BiPAP machine for FREE with any supply order AT YOUR HOME! No one else is committed to providing you with this level of customer service.</p>
    <svg class="abs" style="left:80px;top:352px" width="64" height="14" viewBox="0 0 64 14" role="img" aria-label="Five stars">
      <g fill="#5fd48f"><polygon points="6,0 8,5 13,5 9,8 10.5,13 6,10 1.5,13 3,8 -1,5 4,5"/><polygon transform="translate(13 0)" points="6,0 8,5 13,5 9,8 10.5,13 6,10 1.5,13 3,8 -1,5 4,5"/><polygon transform="translate(26 0)" points="6,0 8,5 13,5 9,8 10.5,13 6,10 1.5,13 3,8 -1,5 4,5"/><polygon transform="translate(39 0)" points="6,0 8,5 13,5 9,8 10.5,13 6,10 1.5,13 3,8 -1,5 4,5"/><polygon transform="translate(52 0)" points="6,0 8,5 13,5 9,8 10.5,13 6,10 1.5,13 3,8 -1,5 4,5"/></g>
    </svg>
    <p class="copy big" style="top:372px">There are many resources available for you on our website at <b>www.RestWellAirway.com</b></p>
    <p class="copy script" style="top:410px">We Love To Talk. You don't have to be a customer to call us, we will answer any questions you have!</p>
    <p class="copy big" style="top:465px">Check out our 5-Star reviews on ReviewHub<br>(By Searching for RestWell Airway)!</p>
  </div>
</section>

</body>
</html>
```